KVOR Individual and Corporate Development Business Card Design

KVOR needs a business card design that is aligned with it's values and targetted markets. Coherent Lattice of Adaptive Reasoning Method's self diagnosis model and tools, which can be used for personal improvement and team/business performance enhancement, is based on the learnings of over 20 years of medical practitioning. KVOR supercharges personal effectiveness and awareness to also increase team and business performance.

The targetted markets are high performance individuals and teams who aspire seek to enhance their capabilities and achieve their absolute best potential.

Look and feel for the business card design we are looking for is high technology, premium, fresh, new and medical.

Target Market(s)

Industry/Entity Type

Business Consultant

Contact Information for Business Card

Logo, Full Name, Title, Phone number, Email, company name, Address,

Font styles to use
Sans Serif

Requirements
Must have
• Tag line: Elevating Potential for Driven and Focused Teams
• Please use same colours as the logo.

```html
<!DOCTYPE html>
<html lang="en">
<head>
<meta charset="utf-8">
<title>KVOR Business Card</title>
<link href="https://fonts.googleapis.com/css2?family=Roboto:ital,wght@0,400;0,500;0,700;0,900;1,400&family=Roboto+Condensed:wght@500;700&display=swap" rel="stylesheet">
<style>
  :root {
    --teal: #00a9c1;
    --grey: #5f6166;
    --text: #4a4c50;
    --paper: #f3f3f3;
    --backdrop: #2a2a2b;
    --white: #ffffff;
  }
  * { margin: 0; padding: 0; box-sizing: border-box; }
  html, body {
    width: 1200px; height: 960px; overflow: hidden;
    background: var(--backdrop);
    font-family: "Roboto", Arial, sans-serif;
  }
  .canvas { position: relative; width: 1200px; height: 960px; }
  .card { position: absolute; width: 600px; height: 343px; }
  .card--front { left: 314px; top: 113px; background: var(--paper); }
  .card--back { left: 311px; top: 472px; background: var(--teal); }

  .brand { position: absolute; left: 0; right: 0; text-align: center; }
  .brand__name {
    display: block;
    font-weight: 900; font-size: 62px; letter-spacing: 4px; line-height: 1;
  }
  .brand__full {
    display: block; margin-top: 14px;
    font-weight: 700; font-size: 16px; line-height: 17px; letter-spacing: 0.3px;
    text-transform: uppercase;
  }
  .card--front .brand { top: 70px; color: var(--teal); }
  .card--back .brand { top: 138px; color: var(--white); }

  .divider { position: absolute; left: 32px; top: 213px; width: 536px; height: 3px; }
  .divider__grey { position: absolute; left: 0; top: 0; width: 134px; height: 3px; background: var(--grey); }
  .divider__teal { position: absolute; left: 134px; top: 1px; right: 0; height: 1.5px; background: var(--teal); }

  .person { position: absolute; left: 32px; top: 230px; }
  .person__name {
    font-family: "Roboto Condensed", Arial, sans-serif;
    font-weight: 700; font-size: 21px; color: var(--teal); line-height: 24px;
  }
  .person__title { font-size: 15px; font-weight: 400; color: var(--text); line-height: 18px; }
  .contact { list-style: none; margin-top: 7px; }
  .contact__item {
    display: flex; align-items: center; gap: 7px;
    font-size: 14.5px; color: var(--text); line-height: 20px;
  }
  .contact__icon { width: 14px; height: 14px; fill: var(--teal); flex: none; }

  .company { position: absolute; right: 32px; top: 232px; text-align: right; color: var(--text); }
  .company__name { font-size: 14.5px; font-weight: 500; line-height: 18px; }
  .company__address { font-size: 14.5px; line-height: 18px; margin-top: 9px; font-style: normal; }

  .tagline {
    position: absolute; left: 0; right: 0; top: 292px; text-align: center;
    color: var(--white); font-style: italic; font-size: 14.5px;
  }
</style>
</head>
<body>
<main class="canvas">
  <section class="card card--front">
    <div class="brand">
      <span class="brand__name">KVOR</span>
      <span class="brand__full">Coherent Lattice of Adaptive<br>Reasoning Method</span>
    </div>
    <div class="divider"><span class="divider__grey"></span><span class="divider__teal"></span></div>
    <div class="person">
      <p class="person__name">DANIEL REYES</p>
      <p class="person__title">CEO/FOUNDER</p>
      <ul class="contact">
        <li class="contact__item">
          <svg class="contact__icon" viewBox="0 0 24 24" aria-hidden="true"><path d="M6.6 10.8a15.1 15.1 0 0 0 6.6 6.6l2.2-2.2c.3-.3.7-.4 1-.2 1.1.4 2.3.6 3.6.6.6 0 1 .4 1 1V20c0 .6-.4 1-1 1A17 17 0 0 1 3 4c0-.6.4-1 1-1h3.5c.6 0 1 .4 1 1 0 1.3.2 2.5.6 3.6.1.3 0 .7-.2 1z"/></svg>
          555 014 2290
        </li>
        <li class="contact__item">
          <svg class="contact__icon" viewBox="0 0 24 24" aria-hidden="true"><path d="M2 6l10 7 10-7v12H2z"/><path d="M2 5h20l-10 6.5z"/></svg>
          hello@kvormethod.com
        </li>
      </ul>
    </div>
    <div class="company">
      <p class="company__name">Coherent Lattice Of<br>Adaptive Reasoning Method</p>
      <address class="company__address">214 Willow Crest Road<br>Juneau, Alaska 99801</address>
    </div>
  </section>

  <section class="card card--back">
    <div class="brand">
      <span class="brand__name">KVOR</span>
      <span class="brand__full">Coherent Lattice of Adaptive<br>Reasoning Method</span>
    </div>
    <p class="tagline">Elevating Potential for Driven and Focused Teams</p>
  </section>
</main>
</body>
</html>
```